Local Flower Farm Needs Business Card Design

I need business cards designed for a flower farm based in Eudora, Kansas.
Business Info:
We are a local cut flower farm located in Eudora, Kansas, founded by Corinne Haldwick. What started as a passion for agriculture and search for more joy in daily life has blossomed into a small business dedicated to providing the community with beautiful, fresh, and sustainable flowers. We specialize in local, seasonal blooms, ensuring that every petal reflects the care and dedication we pour into our craft. Our mission is to deliver the highest quality flowers directly to our customers through local farmers markets and to florists who share our commitment to sustainability. Join us in celebrating the beauty of nature, one bloom at a time!
Contact Details:
Corinne Haldwick
Owner
Phone 913-555-0147
Facebook: Rosalind Thorpe Gardens
Instagram: @RosalindThorpeGardens
Website: RosalindThorpeGardens.example
Target Market(s)
Wholesale to Florists and Direct to Consumer via Farmers Market
Industry/Entity Type
Florist, Farm
Contact Information for Business Card
Name, Contact Info, Logo
Look and feel
Each slider illustrates characteristics of the customer's brand and the style your logo design should communicate.

```html
<!DOCTYPE html>
<html lang="en">
<head>
<meta charset="utf-8">
<title>Rosalind Thorpe Gardens — Business Card</title>
<link rel="stylesheet" href="https://fonts.googleapis.com/css2?family=Tinos:wght@400;700&display=swap">
<style>
  :root {
    --page-bg: #e3e8e9;
    --card-bg: #0a2730;
    --card-ink: #ffffff;
    --divider: #8fa3a8;
    --pattern-dark: #0b2a31;
    --pattern-mid: #1d4a45;
    --pattern-glow: #7fc39d;
  }
  * { margin: 0; padding: 0; box-sizing: border-box; }
  html, body {
    width: 1200px; height: 960px; overflow: hidden;
    background: var(--page-bg);
    font-family: "Tinos", "Times New Roman", serif;
    color: var(--card-ink);
  }
  .card {
    position: absolute;
    left: 249px; width: 702px; height: 400px;
    background: var(--card-bg);
    overflow: hidden;
  }
  .card--front { top: 60px; }
  .card--back { top: 500px; }

  .front-pattern {
    position: absolute; inset: 0;
    background:
      radial-gradient(ellipse 70% 75% at 100% 0%, rgba(127,195,157,0.55) 0%, rgba(29,74,69,0.35) 45%, rgba(11,42,49,0) 75%),
      linear-gradient(160deg, var(--pattern-dark) 0%, var(--pattern-dark) 100%);
  }
  .front-mark {
    position: absolute;
    left: 599px; top: 293px;
    transform: translate(-50%, -50%);
    font-size: 11px; font-weight: 700;
    letter-spacing: 0.5px;
    white-space: nowrap;
    text-align: center;
    line-height: 1.2;
  }

  .brand-seal {
    position: absolute;
    left: 72px; top: 89px;
    width: 222px; height: 222px;
    border: 1px solid var(--card-ink);
    border-radius: 50%;
    display: flex; align-items: center; justify-content: center;
    text-align: center;
  }
  .brand-seal__name {
    font-size: 24px; font-weight: 400;
    line-height: 1.25; letter-spacing: 1px;
  }

  .divider {
    position: absolute;
    left: 351px; top: 52px;
    width: 1px; height: 297px;
    background: var(--divider);
  }

  .contact-block {
    position: absolute;
    left: 392px; top: 106px;
  }
  .person-name {
    font-size: 34px; font-weight: 700;
    letter-spacing: 1px; line-height: 1;
  }
  .person-role {
    font-size: 16px; letter-spacing: 0.8px;
    margin-top: 4px;
  }
  .contact-list {
    list-style: none;
    margin-top: 44px;
  }
  .contact-list li {
    display: flex; align-items: center;
    height: 24px;
    font-size: 17px; letter-spacing: 0.9px;
  }
  .contact-icon {
    width: 16px; height: 16px;
    margin-right: 9px; flex: none;
  }
  .icon-circle { border-radius: 50%; background: var(--card-ink); }
  .icon-square { border: 2px solid var(--card-ink); border-radius: 2px; }
</style>
</head>
<body>

<section class="card card--front">
  <div class="front-pattern" role="img" aria-label="Repeating embossed brand monogram pattern with a soft green foil glow toward the top right"></div>
  <div class="front-mark">Rosalind Thorpe Gardens</div>
</section>

<section class="card card--back">
  <div class="brand-seal">
    <span class="brand-seal__name">Rosalind<br>Thorpe<br>Gardens</span>
  </div>

  <div class="divider"></div>

  <div class="contact-block">
    <h1 class="person-name">Corinne Haldwick</h1>
    <p class="person-role">Owner</p>
    <ul class="contact-list">
      <li>
        <svg class="contact-icon" viewBox="0 0 24 24" aria-hidden="true">
          <path fill="#fff" d="M6.6 10.8a15.1 15.1 0 0 0 6.6 6.6l2.2-2.2a1 1 0 0 1 1-.25 11.4 11.4 0 0 0 3.6.57 1 1 0 0 1 1 1V20a1 1 0 0 1-1 1A17 17 0 0 1 3 4a1 1 0 0 1 1-1h3.5a1 1 0 0 1 1 1c0 1.25.2 2.45.57 3.57a1 1 0 0 1-.25 1z"/>
        </svg>
        913-555-0147
      </li>
      <li><span class="contact-icon icon-circle"></span>Rosalind Thorpe Gardens</li>
      <li><span class="contact-icon icon-square"></span>@RosalindThorpeGardens</li>
      <li>
        <svg class="contact-icon" viewBox="0 0 24 24" aria-hidden="true">
          <g fill="none" stroke="#fff" stroke-width="2">
            <circle cx="12" cy="12" r="10"/>
            <ellipse cx="12" cy="12" rx="4" ry="10"/>
            <line x1="2" y1="12" x2="22" y2="12"/>
          </g>
        </svg>
        RosalindThorpeGardens.example
      </li>
    </ul>
  </div>
</section>

</body>
</html>
```